Web portal for events

The project is about creating a web application - portal for culture events in Denmark.

Design

We aim for very simplistic, light and fully responsive design. The white background is preferable, as well as light color tones. As inspirational points we like the colors used in www.parvolio.com and www.brindlemoor.org

FORMAT AND REQUIREMENTS:
1. Design should be provided based on the wireframes specified as a link below.
2. The design (and all of its pages) should be provided in three resolution variants:
- Desktop
- Tablet
- Phone
3. The design should be provided as PSD, where each page/section should be in its own PSD file
4. All graphical elements in the design should be delivered as single layers which can then be extracted from the PSD.
5. All graphical elements (icons, graphical buttons, etc.) should be provided as vector objects in the PSD, so that they can be exported into different sizes without loss of quality (for responsiveness)
6. The design should use either web safe fonts or Google Fonts.

RESPONSIVENESS
The web application should be visible on any devices (i.e. responsive design)

WIREFRAMES:
https://velkotrams.examplewire.com/projects/fennoplex/prototype/Homepage?key=3b7c19d0f2a84e6c5d1e9a07b4f2c8d6e1a3f590

We expect design of the following wireframes:

Homepage:
https://velkotrams.examplewire.com/projects/fennoplex/Homepage

For arrangører - billede uploaded:
https://velkotrams.examplewire.com/projects/fennoplex/For%20arrang%C3%B8rer%20-%20billede%20uploaded

Further specifications of the project (i.e. functionality, etc.):
https://files.quorvane.net/document/d/8pKw_Rt2mZqLx4NvB7yHc0aEs9uGdJf3TiOb6nVlW1k/edit?usp=sharing

```html
<!DOCTYPE html>
<html lang="da">
<head>
<meta charset="utf-8">
<title>Kulvio – Din guide til kultur og events</title>
<link rel="stylesheet" href="https://fonts.googleapis.com/css2?family=Open+Sans:wght@400;600;700&display=swap">
<style>
:root{
  --green:#2aa84a;
  --red:#e2453a;
  --grey-btn:#8a8a8a;
  --dark-btn:#555;
  --header-bg:#e6e6e6;
  --nav-bg:#ececec;
  --text:#333;
  --line:#dcdcdc;
  --panel:#f2f2f2;
}
*{box-sizing:border-box;margin:0;padding:0}
html,body{width:1164px;height:1200px;overflow:hidden;background:#fff}
body{position:relative;font-family:"Open Sans",Arial,sans-serif;color:var(--text)}

.site-header{position:absolute;left:0;top:0;width:1164px;height:96px;background:var(--header-bg);border-bottom:1px solid #d8d8d8}
.brand{position:absolute;left:90px;top:18px}
.brand-name{font-size:34px;font-weight:400;letter-spacing:8px;color:#222;line-height:42px}
.brand-tagline{font-size:11px;color:#555;margin-top:2px}
.search-input{position:absolute;left:432px;top:38px;width:244px;height:24px;background:#fff;border:1px solid #cfcfcf;border-radius:4px 0 0 4px}
.btn{position:absolute;display:flex;align-items:center;justify-content:center;color:#fff;font-size:12px;font-weight:600;border-radius:3px}
.btn-search{left:674px;top:38px;width:80px;height:24px;background:var(--green);border-radius:0 3px 3px 0}
.btn-grey{background:var(--grey-btn);height:24px;top:38px}
.btn-login{left:982px;top:38px;width:93px;height:24px;background:var(--red)}

.category-nav{position:absolute;left:90px;top:124px;width:986px;height:35px;display:flex;background:var(--nav-bg);border:1px solid #ddd}
.category-nav a{flex:1;display:flex;align-items:center;justify-content:center;font-size:14px;font-weight:400;color:#444;text-decoration:none;border-right:1px solid #ddd}
.category-nav a:last-child{border-right:none}
.category-nav a.active{background:var(--green);color:#fff}

.section-title{position:absolute;font-size:17px;font-weight:600;color:#333;letter-spacing:.2px}
.sort-bar{position:absolute;left:468px;top:190px;display:flex;align-items:center;gap:7px;font-size:11px;color:#888}
.sort-bar .opt{height:20px;padding:0 9px;display:flex;align-items:center;border:1px solid #ddd;color:#777;background:#fff}
.sort-bar .opt.active{background:var(--red);color:#fff;border-color:var(--red)}
.sort-bar .opt.select{width:79px;justify-content:space-between}

.event-card{position:absolute;width:238px;height:230px;border:1px solid var(--line);background:#fff}
.event-card.featured{box-shadow:0 2px 6px rgba(0,0,0,.22)}
.event-img{position:absolute;left:9px;top:8px;width:220px;height:118px}
.event-title{position:absolute;left:10px;top:134px;font-size:18px;color:#333}
.featured .event-title{color:var(--green)}
.event-desc{position:absolute;left:10px;top:161px;font-size:11.5px;color:#999}
.event-date{position:absolute;right:10px;top:161px;font-size:11.5px;color:#333}
.card-btn{position:absolute;top:197px;height:19px;display:flex;align-items:center;justify-content:center;font-size:10.5px;color:#fff;background:var(--dark-btn)}
.card-btn.see{left:9px;width:61px}
.card-btn.fav{left:73px;width:154px}
.featured .card-btn.see{background:var(--green)}

.fav-img{position:absolute;left:873px;width:201px;height:116px}
.fav-dance{top:247px;background:linear-gradient(160deg,#123418,#3c6a2c 50%,#c9c9a0 60%,#1d3a18)}
.fav-sand{top:382px;background:linear-gradient(180deg,#9fb2c8,#b89a74 60%,#8c6e52)}
.fav-square{top:517px;background:linear-gradient(180deg,#b7c7d9,#a48c6a 50%,#6b8a3a)}
.btn-favs{left:874px;top:653px;width:128px;height:30px;background:var(--grey-btn);font-weight:400;font-size:12px;border-radius:0}
.divider{position:absolute;left:875px;top:714px;width:199px;height:1px;background:#ccc}
.newsletter{position:absolute;left:873px;top:779px;width:201px;height:189px;background:var(--panel)}
.newsletter p{position:absolute;left:14px;top:12px;width:180px;font-size:11.3px;line-height:18px;color:#666;text-align:left}
.email-field{position:absolute;left:9px;top:113px;width:183px;height:30px;background:#fff;border:1px solid #ddd;font-size:11px;color:#aaa;padding:8px 13px}
.btn-subscribe{left:125px;top:154px;width:67px;height:25px;background:var(--red);font-size:13px;font-weight:400;border-radius:0}

.pagination{position:absolute;left:360px;top:1014px;height:34px;display:flex;border:1px solid #ddd;border-radius:17px;background:#f4f4f4;overflow:hidden;box-shadow:0 1px 2px rgba(0,0,0,.1)}
.pagination span{width:31px;display:flex;align-items:center;justify-content:center;font-size:13px;font-weight:600;color:#666;border-right:1px solid #ddd}
.pagination span:last-child{border-right:none}
.pagination .first{color:var(--red)}
.pagination .current{background:var(--red);color:#fff}
.pagination .arrow{color:#999;font-weight:400}

.site-footer{position:absolute;left:0;top:1111px;width:1164px;height:89px;background:var(--red)}
.footer-links{position:absolute;left:0;top:0;width:100%;height:45px;display:flex;align-items:center;justify-content:center;font-size:11px;font-weight:600;color:#fff;border-bottom:1px solid #ef7a70}
.footer-links .sep{margin:0 9px}
.copyright{position:absolute;left:90px;top:58px;font-size:11.5px;color:#fff}
.social{position:absolute;top:59px;left:1001px;display:flex;gap:12px}
.social span{width:17px;height:17px;border-radius:50%;background:#fff}
</style>
</head>
<body>

<header class="site-header">
  <div class="brand">
    <div class="brand-name">KULVIO</div>
    <div class="brand-tagline">Dun Guide til kutur og events</div>
  </div>
  <div class="search-input"></div>
  <div class="btn btn-search">Search</div>
  <div class="btn btn-grey" style="left:770px;width:56px">SOG</div>
  <div class="btn btn-grey" style="left:841px;width:128px;font-weight:400">Avanceret sogning</div>
  <div class="btn btn-login">Login / Signup</div>
</header>

<nav class="category-nav">
  <a class="active">ALLE</a><a>MUSIK</a><a>SPORT</a><a>TEATER</a><a>UDSTILLING</a><a>AELDRE</a><a>BORN</a><a>MOTION</a><a>DIVERSE</a>
</nav>

<h2 class="section-title" style="left:89px;top:189px">POPULAERE EVENTS</h2>
<div class="sort-bar">
  <span>Sorter efter</span>
  <span class="opt active">Populaere</span>
  <span class="opt select">Omrade
    <svg width="9" height="6" viewBox="0 0 9 6"><path d="M0 0h9L4.5 6z" fill="#999"/></svg></span>
  <span class="opt">Date</span>
  <span class="opt">Pris</span>
</div>

<article class="event-card featured" style="left:90px;top:249px">
  <div class="event-img" role="img" aria-label="Oppustelig kunstinstallation i grønne og røde farver" style="background:linear-gradient(120deg,#1e3a6e,#3fc27a 40%,#b83a4a 70%,#6bd68f)"></div>
  <div class="event-title">Kunst pa Velmor</div><div class="event-desc">Pellentesque elei...</div><div class="event-date">Aug 2, 2014</div>
  <div class="card-btn see">Se event</div><div class="card-btn fav">Tilfoj til mine favoritter</div>
</article>
<article class="event-card" style="left:351px;top:249px">
  <div class="event-img" role="img" aria-label="Besøgende i en hvid kunstudstilling" style="background:linear-gradient(180deg,#e8e8e8,#bdbdbd 60%,#6f6f6f)"></div>
  <div class="event-title">Kunst pa Velmor</div><div class="event-desc">Pellentesque elei...</div><div class="event-date">Aug 2, 2014</div>
  <div class="card-btn see">Se event</div><div class="card-btn fav">Tilfoj til mine favoritter</div>
</article>
<article class="event-card" style="left:610px;top:249px">
  <div class="event-img" role="img" aria-label="Byplads med røde flader og hvide gynger" style="background:linear-gradient(180deg,#8fa9c9,#c9c3bb 40%,#d8404a 80%,#e25c63)"></div>
  <div class="event-title">Kunst pa Velmor</div><div class="event-desc">Pellentesque elei...</div><div class="event-date">Aug 2, 2014</div>
  <div class="card-btn see">Se event</div><div class="card-btn fav">Tilfoj til mine favoritter</div>
</article>

<article class="event-card" style="left:90px;top:503px">
  <div class="event-img" role="img" aria-label="Kridtklint ved havet med kirke og skov" style="background:linear-gradient(100deg,#a9b9cc,#8d9aa6 35%,#5d6b43 60%,#c9c6bd)"></div>
  <div class="event-title">Kunst pa Velmor</div><div class="event-desc">Pellentesque elei...</div><div class="event-date">Aug 2, 2014</div>
  <div class="card-btn see">Se event</div><div class="card-btn fav">Tilfoj til mine favoritter</div>
</article>
<article class="event-card" style="left:351px;top:503px">
  <div class="event-img" role="img" aria-label="Slot under blå himmel med græsvold" style="background:linear-gradient(180deg,#4a78b4,#9bb6d6 45%,#a89f86 65%,#3e4a2c)"></div>
  <div class="event-title">Kunst pa Velmor</div><div class="event-desc">Pellentesque elei...</div><div class="event-date">Aug 2, 2014</div>
  <div class="card-btn see">Se event</div><div class="card-btn fav">Tilfoj til mine favoritter</div>
</article>
<article class="event-card" style="left:610px;top:503px">
  <div class="event-img" role="img" aria-label="Farvefestival med pink og gult pulver" style="background:linear-gradient(110deg,#e64fa8,#f2e24a 45%,#e35aa0 70%,#6bc3e0)"></div>
  <div class="event-title">Kunst pa Velmor</div><div class="event-desc">Pellentesque elei...</div><div class="event-date">Aug 2, 2014</div>
  <div class="card-btn see">Se event</div><div class="card-btn fav">Tilfoj til mine favoritter</div>
</article>

<article class="event-card" style="left:90px;top:755px">
  <div class="event-img" role="img" aria-label="Havn med farverige huse og sejlbåde" style="background:linear-gradient(180deg,#b9cde0,#c8a867 40%,#6e5a46 70%,#3c3f3a)"></div>
  <div class="event-title">Kunst pa Velmor</div><div class="event-desc">Pellentesque elei...</div><div class="event-date">Aug 2, 2014</div>
  <div class="card-btn see">Se event</div><div class="card-btn fav">Tilfoj til mine favoritter</div>
</article>
<article class="event-card" style="left:351px;top:755px">
  <div class="event-img" role="img" aria-label="Vennegruppe med cykel i sollys" style="background:linear-gradient(120deg,#d9d2a8,#7a6a4c 45%,#3a2e24)"></div>
  <div class="event-title">Kunst pa Velmor</div><div class="event-desc">Pellentesque elei...</div><div class="event-date">Aug 2, 2014</div>
  <div class="card-btn see">Se event</div><div class="card-btn fav">Tilfoj til mine favoritter</div>
</article>
<article class="event-card" style="left:610px;top:755px">
  <div class="event-img" role="img" aria-label="Sø i en park med træer" style="background:linear-gradient(180deg,#7fd6c0,#2f4a36 40%,#1f6f86 65%,#1e5f7a)"></div>
  <div class="event-title">Kunst pa Velmor</div><div class="event-desc">Pellentesque elei...</div><div class="event-date">Aug 2, 2014</div>
  <div class="card-btn see">Se event</div><div class="card-btn fav">Tilfoj til mine favoritter</div>
</article>

<nav class="pagination">
  <span class="arrow">&#8249;</span><span class="first">1</span><span class="current">2</span><span>3</span><span>4</span><span>5</span><span class="arrow">&#8250;</span>
</nav>

<h2 class="section-title" style="left:874px;top:190px">MINE FAVOURITTER</h2>
<div class="fav-img fav-dance" role="img" aria-label="Danseforestilling på mørk grøn scene"></div>
<div class="fav-img fav-sand" role="img" aria-label="Sandskulptur af by med kupler"></div>
<div class="fav-img fav-square" role="img" aria-label="Plads med bygninger og græsplæne"></div>
<div class="btn btn-favs">Se mine Favouritter</div>
<div class="divider"></div>
<h2 class="section-title" style="left:873px;top:748px">NYHEDSBREV</h2>
<div class="newsletter">
  <p>Lorem ipsum dolor sit amet, consectetur adipiscing elit. Phasellus at magna id dolor eleifend lobortis. Sed iaculis mauris at consequat pulvinar.</p>
  <div class="email-field">Email ID</div>
  <div class="btn btn-subscribe">TILMED</div>
</div>

<footer class="site-footer">
  <div class="footer-links">
    <span>Om Kulvio</span><span class="sep">|</span><span>Vilkar &amp; betingelser</span><span class="sep">|</span><span>Kobspolitik</span><span class="sep">|</span><span>Nyhedsbrev</span><span class="sep">|</span><span>Kontakt</span><span class="sep">|</span><span>Login/Registrer</span><span class="sep">|</span><span>Haelp</span><span class="sep">|</span><span>ForArrangoreer</span><span class="sep">|</span><span>For Kommuner og turistforeninger</span>
  </div>
  <div class="copyright">Yoursite © 2014 All Rights Reserved.</div>
  <div class="social"><span></span><span></span><span></span></div>
</footer>

</body>
</html>
```